Create modern and sleek business card for luxury real estate company

We're a "boutique" real estate office looking for a design that gets across a highly modern luxury brand. Blacks and whites are probably the best colors unless we try a silver foil for the logo. I've attached a version of our current logo here. I'd like to swap out the current font on there with Gotham Light Regular.

I'm looking to have one side of the card have the logo with the space for our agents info on the other side.

Target Market(s)

Young professionals in a "luxury" headspace

Industry/Entity Type

Real estate

Contact Information for Business Card

A place for agent name, cell number, website. The slogan "Simply Rethinking Real Estate".

Font styles to use
Other font styles liked:
• Gotham Regular

Colors

Designer to choose only greyscale colors for use in the design.

Requirements
Must have
• Matte black as the background color. Clean lines and use of contrast. A specific design aspect that will use silver foil.
Nice to have
• Up in the air on integrating a QR code
Should not have
• Any houses or other real estate related design (ex: a clip art house)

```html
<!DOCTYPE html>
<html lang="en">
<head>
<meta charset="utf-8">
<title>Lumen Estates – Business Card</title>
<link rel="stylesheet" href="https://fonts.googleapis.com/css2?family=Libre+Baskerville:wght@400;700&family=Lato:wght@400&display=swap">
<style>
  :root {
    --stage: #9a9a9a;
    --card-dark: #333333;
    --card-light: #ffffff;
    --ink-light: #f2f2f2;
    --ink-dark: #1e1e1e;
    --rule: #8a8a8a;
    --shadow: rgba(0, 0, 0, 0.35);
  }
  * { box-sizing: border-box; margin: 0; padding: 0; }
  html, body {
    width: 1200px;
    height: 1200px;
    overflow: hidden;
    background: var(--stage);
  }
  .canvas {
    position: relative;
    width: 1200px;
    height: 1200px;
  }
  .card {
    position: absolute;
    top: 303px;
    width: 368px;
    height: 594px;
    box-shadow: 3px 4px 6px var(--shadow);
    overflow: hidden;
  }
  .card--front { left: 200px; background: var(--card-dark); }
  .card--back { left: 598px; background: var(--card-light); }

  .pattern-area {
    position: absolute;
    inset: 0 0 110px 0;
    background: radial-gradient(circle at 55% 45%, #393939 0%, var(--card-dark) 70%);
  }

  .brand {
    position: absolute;
    display: flex;
    align-items: center;
    gap: 18px;
  }
  .brand__mark {
    flex: none;
    border-radius: 50%;
    border: 2px solid currentColor;
  }
  .brand__name {
    font-family: "Libre Baskerville", serif;
    font-weight: 400;
    font-size: 34px;
    line-height: 1.15;
    letter-spacing: 1px;
    text-transform: uppercase;
  }
  .card--front .brand { left: 27px; top: 445px; color: var(--ink-light); }
  .card--front .brand__mark { width: 89px; height: 89px; }
  .card--back .brand { left: 40px; top: 100px; color: var(--ink-dark); }
  .card--back .brand__mark { width: 80px; height: 80px; }

  .wave {
    position: absolute;
    left: 0;
    top: 0;
    width: 368px;
    height: 594px;
  }

  .agent {
    position: absolute;
    left: 0;
    right: 0;
    top: 340px;
    text-align: center;
    color: var(--ink-light);
  }
  .agent__name {
    font-family: "Libre Baskerville", serif;
    font-weight: 700;
    font-size: 21px;
    letter-spacing: 1px;
    text-transform: uppercase;
  }
  .agent__role {
    font-family: "Lato", sans-serif;
    font-size: 16px;
    margin-top: 2px;
  }
  .contact-icons {
    display: flex;
    justify-content: center;
    align-items: center;
    gap: 5px;
    margin-top: 16px;
  }
  .contact-icons__rule {
    width: 50px;
    height: 1px;
    background: var(--rule);
    margin: 0 6px;
  }
  .contact-icons__item {
    width: 25px;
    height: 25px;
    border-radius: 3px;
    background: var(--card-light);
    display: flex;
    align-items: center;
    justify-content: center;
  }
  .contact-list {
    font-family: "Lato", sans-serif;
    font-size: 16px;
    line-height: 22px;
    margin-top: 9px;
  }
  .divider {
    width: 196px;
    height: 1px;
    background: var(--rule);
    margin: 9px auto 9px;
  }
</style>
</head>
<body>
<main class="canvas">

  <section class="card card--front" aria-label="Card front">
    <div class="pattern-area" role="img" aria-label="Faint repeated brand emblem pattern on matte black"></div>
    <div class="brand">
      <span class="brand__mark"></span>
      <span class="brand__name">Lumen<br>Estates</span>
    </div>
  </section>

  <section class="card card--back" aria-label="Card back">
    <div class="brand">
      <span class="brand__mark"></span>
      <span class="brand__name">Lumen<br>Estates</span>
    </div>

    <svg class="wave" viewBox="0 0 368 594" aria-hidden="true">
      <path d="M0,268 C70,300 150,285 230,238 C275,212 320,205 368,248 L368,260 C320,218 275,226 232,250 C150,298 70,312 0,282 Z" fill="var(--card-dark)"/>
      <path d="M0,292 C70,326 150,306 232,258 C276,232 322,226 368,268 L368,594 L0,594 Z" fill="var(--card-dark)"/>
    </svg>

    <div class="agent">
      <p class="agent__name">Adrian Vale</p>
      <p class="agent__role">Managing Director</p>

      <div class="contact-icons">
        <span class="contact-icons__rule"></span>
        <span class="contact-icons__item" aria-label="Phone">
          <svg width="15" height="15" viewBox="0 0 16 16"><path d="M2 6 C2 3 5 2 8 2 C11 2 14 3 14 6 L11 7 L10 5 L6 5 L5 7 Z M4 8 L12 8 L13 14 L3 14 Z" fill="var(--ink-dark)"/></svg>
        </span>
        <span class="contact-icons__item" aria-label="Email">
          <svg width="15" height="15" viewBox="0 0 16 16"><rect x="1.5" y="3.5" width="13" height="9" fill="none" stroke="var(--ink-dark)" stroke-width="1.5"/><path d="M1.5 3.5 L8 9 L14.5 3.5" fill="none" stroke="var(--ink-dark)" stroke-width="1.5"/></svg>
        </span>
        <span class="contact-icons__item" aria-label="Website">
          <svg width="15" height="15" viewBox="0 0 16 16"><circle cx="8" cy="8" r="6.5" fill="var(--ink-dark)"/><path d="M8 1.5 C5 5 5 11 8 14.5 M8 1.5 C11 5 11 11 8 14.5 M1.5 8 H14.5" fill="none" stroke="var(--card-light)" stroke-width="0.9"/></svg>
        </span>
        <span class="contact-icons__rule"></span>
      </div>

      <div class="contact-list">
        <p>044-555 018 273</p>
        <p>hello@lumenestates.com</p>
        <p>www.lumenestates.com</p>
      </div>
      <div class="divider"></div>
      <div class="contact-list" style="margin-top:0">
        <p>18, Harbour Row Lane</p>
        <p>20814, Country Name</p>
      </div>
    </div>
  </section>

</main>
</body>
</html>
```